Quillbay.vc needs a better website design!

We need a new and better website for Quillbay.vc. We're a Canadian venture capital firm that invests in innovative entrepreneurs. We compete against the following websites: tormelo.vc, brightvalefund.ca, kestrowvc.com, and dovaran.vc. We're a diverse group of partners and we're dedicated to the founders we invest in.
Updates

I don’t really like stock photos of random people as part of the website design…so please try to stay away from using those images. Thanks, Owen

Target Market(s)

Canadian entrepreneurs and investors

Industry/Entity Type

Venture capital, finance, investment, entrepreneurship

Coding

Coded - Design and coding required

Number of Pages Required

4 page

Font styles to use
Sans Serif

Colors

Designer to choose colors to be used in the design.

Requirements
Must have
• Clean crisp overall design. Fast and to the point.
Nice to have
• Check out www.quillbay.vc - I did it myself and it is too basic and too wordy.
Should not have
• No stock images with random people in them! Not too wordy or with too many large images that are slow to load.

```html
<!DOCTYPE html>
<html lang="en">
<head>
<meta charset="utf-8">
<title>Quillbay.vc — Venture Capital</title>
<link href="https://fonts.googleapis.com/css2?family=Poppins:wght@300;400;500;600;700&display=swap" rel="stylesheet">
<style>
:root{
  --green:#86a13a;
  --green-dark:#6f8a2a;
  --green-soft:#a9bd6a;
  --card:#eef2d9;
  --card-line:#dfe7bd;
  --ink:#2d2d2d;
  --muted:#555;
  --footer:#f6f6f6;
  --white:#fff;
}
*{margin:0;padding:0;box-sizing:border-box}
html,body{width:1200px;height:2299px;overflow:hidden}
body{position:relative;font-family:"Poppins",sans-serif;color:var(--ink);background:var(--white)}
.abs{position:absolute}

/* header */
.site-header{position:absolute;left:0;top:0;width:1200px;height:96px;background:var(--white);border-bottom:1px solid #e6e6e6}
.brand{position:absolute;left:161px;top:12px;width:90px;text-align:center}
.brand-dot{width:44px;height:44px;border:3px solid var(--green);border-radius:50%;margin:0 auto 6px}
.brand-name{font-weight:600;font-size:14px;color:var(--green);letter-spacing:.5px}
.nav a{position:absolute;top:38px;font-size:14px;color:#444;text-decoration:none}
.nav .active{left:705px;top:0;width:63px;height:101px;background:#f1f1f1;border-bottom:5px solid var(--green);color:var(--green);text-align:center;padding-top:38px}

/* hero */
.hero{position:absolute;left:0;top:96px;width:1200px;height:545px;
  background:linear-gradient(180deg,#5b5a50 0%,#6c6a5c 22%,#3d5b4e 45%,#2f6f7a 62%,#245a66 78%,#1e3a30 100%)}
.hero-shade{position:absolute;inset:0;background:rgba(20,25,30,.28)}
.hero-title{position:absolute;left:40px;top:50px;width:1120px;text-align:center;color:var(--white);font-size:30px;line-height:51px;font-weight:400;white-space:nowrap}
.numbers-title{position:absolute;left:0;top:229px;width:1200px;text-align:center;color:var(--white);font-size:18px;font-weight:500}
.rule{position:absolute;top:242px;height:1px;background:rgba(255,255,255,.45);width:210px}
.stat-label{color:var(--white);font-size:15px}
.stat-num{color:var(--green-soft);font-size:37px;font-weight:500;line-height:1}
.dot{width:7px;height:7px;border-radius:50%;background:var(--white)}

/* intro */
.intro{position:absolute;left:0;top:710px;width:1200px;text-align:center;font-size:27px;line-height:37px;color:#444;font-weight:300}
.card-text{position:absolute;font-size:15px;line-height:25px;color:#333;white-space:nowrap}

/* portfolio */
.section-title{position:absolute;left:0;width:1200px;text-align:center;font-size:25px;color:#444;font-weight:300}
.logo-grid{position:absolute;left:161px;top:1259px;width:877px;display:grid;grid-template-columns:repeat(5,154px);column-gap:26.75px;row-gap:22px}
.logo-tile{height:66px;background:var(--white);border:1px solid #ececec;box-shadow:0 2px 6px rgba(0,0,0,.06);display:flex;align-items:center;justify-content:center;font-size:18px;font-weight:600;color:#2b2b2b}

/* cta */
.cta{position:absolute;left:0;top:1515px;width:1200px;height:450px;
  background:linear-gradient(180deg,#3f4540 0%,#3b4a3a 40%,#2b3a28 75%,#203020 100%)}
.cta h2{position:absolute;left:0;top:162px;width:1200px;text-align:center;color:var(--white);font-size:50px;line-height:63px;font-weight:500}
.cta p{position:absolute;left:0;top:314px;width:1200px;text-align:center;color:var(--green);font-size:27px}

/* footer */
.site-footer{position:absolute;left:0;top:1965px;width:1200px;height:270px;background:var(--footer)}
.foot-h{position:absolute;font-size:20px;font-weight:500;color:#2b2b2b}
.foot-links{position:absolute;left:161px;top:95px;list-style:none}
.foot-links li{font-size:14px;line-height:32.5px;color:#333}
.foot-links li::before{content:"›";margin-right:9px;color:#555}
.foot-email{position:absolute;left:424px;top:96px;font-size:14px;color:#333}
.foot-email b{font-weight:600}
.social{position:absolute;top:180px;width:30px;height:30px;border-radius:50%}
.foot-brand{position:absolute;left:870px;top:68px;width:168px;text-align:center}
.foot-brand .ring{width:96px;height:96px;border:5px solid var(--green);border-radius:50%;margin:0 auto 14px}
.foot-brand .name{font-size:28px;font-weight:700;color:var(--green)}
.copyright{position:absolute;left:0;top:2235px;width:1200px;height:64px;background:var(--green);color:var(--white);font-size:14px;text-align:center;line-height:50px}
</style>
</head>
<body>

<header class="site-header">
  <div class="brand"><div class="brand-dot"></div><div class="brand-name">QUILLBAY.VC</div></div>
  <nav class="nav">
    <a class="active" href="#">Home</a>
    <a href="#" style="left:809px">What</a>
    <a href="#" style="left:897px">Who</a>
    <a href="#" style="left:978px">Portfolio</a>
  </nav>
</header>

<section class="hero" role="img" aria-label="Mountain lake with forested shores and snowy peaks">
  <div class="hero-shade"></div>
  <h1 class="hero-title">Quillbay.vc is a venture capital firm that invests in innovative<br>seed-stage technology companies in Western Canada focused<br>on B2B and SaaS markets.</h1>
  <div class="rule" style="left:263px"></div>
  <div class="rule" style="left:723px"></div>
  <div class="numbers-title">Quillbay.vc in numbers</div>
  <div class="abs stat-label" style="left:0;top:272px;width:1200px;text-align:center">Follow-on financings</div>
  <div class="abs stat-num" style="left:0;top:316px;width:1178px;text-align:center">07</div>
  <div class="abs dot" style="left:589px;top:359px"></div>
  <div class="abs" style="left:449px;top:350px;width:286px;height:286px;border-radius:50%;background:rgba(255,255,255,.08)"></div>
  <div class="abs" style="left:493px;top:394px;width:198px;height:198px;border-radius:50%;border:5px solid rgba(255,255,255,.92)"></div>
  <div class="abs stat-label" style="left:290px;top:446px;width:110px;text-align:right;line-height:18px">Portfolio companies</div>
  <div class="abs stat-num" style="left:413px;top:452px">10</div>
  <div class="abs dot" style="left:462px;top:466px"></div>
  <div class="abs dot" style="left:715px;top:466px"></div>
  <div class="abs stat-num" style="left:733px;top:450px">100</div>
  <div class="abs stat-label" style="left:802px;top:446px;line-height:18px">+<br>Employees</div>
</section>

<p class="intro">We are serial entrepreneurs and venture<br>capital investors who provide</p>

<svg class="abs" style="left:161px;top:828px" width="878" height="270" viewBox="0 0 878 270" aria-hidden="true">
  <path d="M12 1H359L397 131L359 268H12Q1 268 1 257V12Q1 1 12 1Z" fill="var(--card)" stroke="var(--card-line)"/>
  <path d="M515 1H865Q877 1 877 12V257Q877 268 865 268H515L477 131Z" fill="var(--card)" stroke="var(--card-line)"/>
  <circle cx="438" cy="131" r="78" fill="#c2d190"/>
  <circle cx="438" cy="131" r="59" fill="#93ad4d"/>
  <circle cx="438" cy="131" r="36" fill="none" stroke="#fff" stroke-width="4"/>
  <g fill="none" stroke="#8a8a8a" stroke-width="3">
    <rect x="37" y="107" width="13" height="18" rx="2"/>
    <rect x="57" y="95" width="13" height="30" rx="2"/>
    <rect x="77" y="80" width="13" height="45" rx="2"/>
    <rect x="97" y="64" width="13" height="61" rx="2"/>
  </g>
  <path d="M38 83Q70 78 92 56" fill="none" stroke="var(--green)" stroke-width="3"/>
  <path d="M84 54L94 52L92 62" fill="none" stroke="var(--green)" stroke-width="3"/>
  <g fill="none" stroke="#8a8a8a" stroke-width="3">
    <circle cx="785" cy="65" r="11"/>
    <path d="M766 115V96Q766 82 785 82Q800 82 803 92"/>
    <path d="M766 115H793"/>
  </g>
  <circle cx="811" cy="106" r="18" fill="none" stroke="var(--green)" stroke-width="3"/>
  <text x="811" y="114" text-anchor="middle" font-family="Poppins,sans-serif" font-size="22" fill="var(--green)">$</text>
</svg>
<p class="card-text" style="left:195px;top:968px">Mentoring and strategic advice<br>to help you grow your company quickly<br>and efficiently</p>
<p class="card-text" style="left:692px;top:968px;width:300px;text-align:right">Investor introductions to help you<br>raise additional follow-on funding<br>for your startup</p>

<h2 class="section-title" style="top:1185px">Check out our innovative portfolio companies!</h2>
<div class="logo-grid">
  <div class="logo-tile">Vantrelle</div>
  <div class="logo-tile">Dryhollow</div>
  <div class="logo-tile">Mirelune</div>
  <div class="logo-tile">Oxtavo</div>
  <div class="logo-tile">Quendra</div>
  <div class="logo-tile">Zalmoor</div>
  <div class="logo-tile">Brevitto</div>
  <div class="logo-tile">Portelyn</div>
  <div class="logo-tile">Homvessa</div>
  <div class="logo-tile">Vitarenne</div>
</div>

<section class="cta" role="img" aria-label="Misty green forested mountains">
  <h2>If you have what we’re<br>looking for</h2>
  <p>Contact us today</p>
</section>

<footer class="site-footer">
  <h3 class="foot-h" style="left:161px;top:54px">Quick Links</h3>
  <ul class="foot-links"><li>Home</li><li>What</li><li>Who</li><li>Portfolio</li></ul>
  <h3 class="foot-h" style="left:424px;top:54px">Get In Touch</h3>
  <p class="foot-email"><b>Email:</b>&nbsp; info@quillbay.vc</p>
  <h3 class="foot-h" style="left:424px;top:138px">Follow Us</h3>
  <div class="social" style="left:425px;background:#2aa9e0" role="img" aria-label="Social profile"></div>
  <div class="social" style="left:462px;background:#1e84bf" role="img" aria-label="Professional network profile"></div>
  <div class="foot-brand"><div class="ring"></div><div class="name">QUILLBAY.VC</div></div>
</footer>
<div class="copyright">Copyright © 2021 Quillbay.vc - All Rights Reserved.</div>

</body>
</html>
```